Bright Campus Network Sign

We need a sign that can be displayed on the front fence of schools that shows that will proudly proclaim that the school is an BCN School
The Bright Campus Network is one of the world's leading organisations suppprting schools to become innovative and adaptive organisations.
Updates

The signs are being cut from 2400x1200 boards Signs are 55x40 can be either orientation

Target Market(s)

Parents and educators

Industry/Entity Type

Education

Requirements
Must have
• Edgy. Professional. NOT conservative. Crisp.
• Colours and styles to match existing logos
Nice to have
• The Marlowe Advisory logo is just for reference as it is the parent company. ONLY want reference to BCN.
• Keep it simple. Not too busy. Elegant but edgy
Should not have
• No symbols to do with traditioanl education. NO PENS, MORTAR BOARDS, BOOKS

```html
<!DOCTYPE html>
<html lang="en">
<head>
<meta charset="utf-8">
<title>Bright Campus Network Sign</title>
<link rel="stylesheet" href="https://fonts.googleapis.com/css2?family=Cinzel:wght@500;600&display=swap">
<style>
  :root {
    --sign-white: #ffffff;
    --brand-purple: #522d80;
    --brand-green: #5b7d36;
    --soft-purple: #7a5aa6;
    --soft-green: #7f9c5a;
  }
  html, body {
    margin: 0;
    padding: 0;
    overflow: hidden;
    background: var(--sign-white);
  }
  .sign {
    position: relative;
    width: 1200px;
    height: 874px;
    overflow: hidden;
    background: var(--sign-white);
    font-family: "Cinzel", "Times New Roman", serif;
  }
  .growth-artwork {
    position: absolute;
    left: 0;
    top: 0;
    width: 760px;
    height: 874px;
  }
  .brand-lockup {
    position: absolute;
    right: 92px;
    top: 168px;
    width: 330px;
    text-align: center;
    color: var(--brand-purple);
    font-weight: 500;
    line-height: 1;
  }
  .brand-initials {
    font-size: 84px;
    letter-spacing: -2px;
  }
  .brand-name {
    margin-top: 14px;
    font-size: 30px;
    letter-spacing: 0.5px;
  }
  .brand-name-second {
    margin-top: 4px;
    font-size: 19px;
    letter-spacing: 1px;
  }
  .tagline {
    position: absolute;
    right: 86px;
    top: 488px;
    margin: 0;
    text-align: right;
    font-weight: 500;
    font-size: 90px;
    line-height: 104px;
    letter-spacing: -1px;
  }
  .tagline-line { display: block; }
  .tagline-green { color: var(--brand-green); }
  .tagline-purple { color: var(--brand-purple); }
</style>
</head>
<body>
  <main class="sign">
    <svg class="growth-artwork" viewBox="0 0 760 874" role="img" aria-label="Large decorative growth illustration in purple and green, figures rising into a canopy of leaves">
      <defs>
        <linearGradient id="artworkTone" x1="0" y1="1" x2="1" y2="0">
          <stop offset="0" stop-color="#7f9c5a" stop-opacity="0.55"/>
          <stop offset="1" stop-color="#7a5aa6" stop-opacity="0.45"/>
        </linearGradient>
      </defs>
      <path d="M0 0 H760 V420 H300 V874 H0 Z" fill="url(#artworkTone)"/>
    </svg>

    <div class="brand-lockup">
      <div class="brand-initials">BCN</div>
      <div class="brand-name">BRIGHT CAMPUS</div>
      <div class="brand-name-second">NETWORK</div>
    </div>

    <h1 class="tagline">
      <span class="tagline-line tagline-green">Transforming</span>
      <span class="tagline-line tagline-green">Schools</span>
      <span class="tagline-line tagline-purple">Together</span>
    </h1>
  </main>
</body>
</html>
```